Business Card Design

We are a commercial real estate brokerage in San Francisco, leasing office buildings downtown.
I would like a clean, elegant look. Simple but powerful .

Industry/Entity Type

Business

Contact Information for Business Card

Derek Holloway
lic# 07258143
415.555.0172
derek@velt-commercial.example
velt-commercial.example

```html
<!DOCTYPE html>
<html lang="en">
<head>
<meta charset="utf-8">
<title>Velt Commercial – Business Card</title>
<link rel="stylesheet" href="https://fonts.googleapis.com/css2?family=Jost:wght@600&family=Open+Sans:wght@400;600&display=swap">
<style>
  :root {
    --backdrop: #2c2d31;
    --slate: #7587a6;
    --slate-deep: #66789a;
    --paper: #ffffff;
    --ink: #1f1f22;
    --rule: #3a3a3e;
  }
  * { margin: 0; padding: 0; box-sizing: border-box; }
  html, body { width: 1200px; height: 864px; overflow: hidden; }
  body {
    background: var(--backdrop);
    position: relative;
    font-family: "Open Sans", Arial, sans-serif;
  }
  .card {
    position: absolute;
    left: 340px;
    width: 520px;
    height: 298px;
    overflow: hidden;
    box-shadow: 0 12px 30px rgba(0,0,0,.45);
  }
  /* Front face */
  .card-front {
    top: 92px;
    background: var(--slate);
    display: flex;
    align-items: center;
    justify-content: center;
  }
  .front-wordmark {
    font-family: "Jost", "Futura", sans-serif;
    font-weight: 600;
    color: var(--paper);
    text-align: center;
    line-height: 0.95;
    text-transform: uppercase;
  }
  .front-wordmark .word-main { display: block; font-size: 68px; letter-spacing: 1px; }
  .front-wordmark .word-sub { display: block; font-size: 29px; letter-spacing: 1px; }

  /* Back face */
  .card-back {
    top: 474px;
    background: linear-gradient(135deg, #f4f4f4 0%, var(--paper) 45%, #f6f6f6 100%);
  }
  .brand {
    position: absolute;
    left: 38px;
    top: 42px;
    display: flex;
    align-items: center;
    gap: 14px;
  }
  .brand-square {
    width: 26px;
    height: 26px;
    background: var(--slate);
  }
  .brand-divider {
    width: 2px;
    height: 70px;
    background: var(--rule);
  }
  .brand-name {
    font-family: "Jost", "Futura", sans-serif;
    font-weight: 600;
    color: var(--slate);
    text-transform: uppercase;
    line-height: 0.9;
  }
  .brand-name .word-main { display: block; font-size: 42px; }
  .brand-name .word-sub { display: block; font-size: 19px; letter-spacing: .5px; }

  .contact {
    position: absolute;
    right: 30px;
    top: 132px;
    text-align: right;
  }
  .contact-name {
    font-weight: 600;
    font-size: 19px;
    color: var(--slate);
    margin-bottom: 10px;
    letter-spacing: .3px;
  }
  .contact-line {
    display: flex;
    justify-content: flex-end;
    align-items: center;
    gap: 8px;
    font-size: 13.5px;
    color: var(--ink);
    height: 21px;
  }
  .contact-line svg { width: 12px; height: 12px; fill: none; stroke: var(--slate); stroke-width: 1.6; }
  .contact-line svg .solid { fill: var(--slate); stroke: none; }

  .license-band {
    position: absolute;
    left: 0; right: 0; bottom: 0;
    height: 66px;
    background: var(--slate);
  }
  .license {
    position: absolute;
    left: 0;
    width: 230px;
    bottom: 20px;
    text-align: center;
    color: var(--paper);
    font-weight: 600;
    font-size: 15px;
    letter-spacing: .8px;
  }
</style>
</head>
<body>

  <section class="card card-front" aria-label="Card front">
    <h1 class="front-wordmark">
      <span class="word-main">Velt</span>
      <span class="word-sub">Commercial</span>
    </h1>
  </section>

  <section class="card card-back" aria-label="Card back">
    <div class="brand">
      <span class="brand-square"></span>
      <span class="brand-divider"></span>
      <div class="brand-name">
        <span class="word-main">Velt</span>
        <span class="word-sub">Commercial</span>
      </div>
    </div>

    <div class="contact">
      <p class="contact-name">Derek Holloway</p>
      <p class="contact-line">415.555.0172
        <svg viewBox="0 0 12 12" aria-hidden="true"><path class="solid" d="M2.2 1l2 .2.8 2.4-1.2 1a6 6 0 0 0 3.1 3.1l1-1.2 2.4.8.2 2c-.3.5-.8.7-1.3.7C4.5 10 2 7.5 1.5 2.3c0-.5.2-1 .7-1.3z"/></svg>
      </p>
      <p class="contact-line">derek@velt-commercial.example
        <svg viewBox="0 0 12 12" aria-hidden="true"><rect x="1" y="2.5" width="10" height="7"/><path d="M1 2.5l5 4 5-4"/></svg>
      </p>
      <p class="contact-line">velt-commercial.example
        <svg viewBox="0 0 12 12" aria-hidden="true"><path d="M5 7l2-2M4.2 5.6L2.8 7a1.7 1.7 0 0 0 2.4 2.4l1.4-1.4M7.8 6.4L9.2 5a1.7 1.7 0 0 0-2.4-2.4L5.4 4"/></svg>
      </p>
    </div>

    <div class="license-band">
      <p class="license">LIC# 07258143</p>
    </div>
  </section>

</body>
</html>
```